Velvette by Marisa Dunn business cards

I am after a business card that will fit the name of my business - velvette.
I want something classy and sexy and nothing tacky.
Ideas that I like are Zebra print backgrounds glitter back grounds
Two ideas I had were
1. Zebra print in black and white, the name Velvette by Marisa Dunn and a shilouette of a woman laying on top of the name. Or instead of zebra a glitter background.
2. Idea very similar except for instead of a woman a pair of lips maybe a hot pink glitter or a gold glitter depending on background with the business name between the lips.
Or you can do something completely different.

```html
<!DOCTYPE html>
<html lang="en">
<head>
<meta charset="utf-8">
<title>Velvette by Marisa Dunn – Business Cards</title>
<link rel="stylesheet" href="https://fonts.googleapis.com/css2?family=Nunito:wght@800&display=swap">
<style>
  :root {
    --page-bg: #ffffff;
    --ink: #0b0b0b;
    --gold: #d4aa3c;
    --gold-light: #f2d77a;
    --gold-deep: #a9801f;
    --pink: #ee4fa5;
    --pink-deep: #c92f85;
    --white: #ffffff;
    --card-w: 525px;
    --card-h: 300px;
    --card-radius: 30px;
  }
  html, body {
    margin: 0;
    padding: 0;
    width: 1200px;
    height: 900px;
    overflow: hidden;
    background: var(--page-bg);
  }
  .sheet {
    position: relative;
    width: 1200px;
    height: 900px;
    display: flex;
    align-items: center;
    justify-content: center;
    gap: 50px;
    font-family: "Nunito", Arial, sans-serif;
  }
  .card {
    position: relative;
    width: var(--card-w);
    height: var(--card-h);
    border-radius: var(--card-radius);
    overflow: hidden;
    box-shadow: 0 18px 30px rgba(0, 0, 0, 0.12);
  }
  .card__pattern {
    position: absolute;
    inset: 0;
  }
  .card--front .card__pattern {
    background: linear-gradient(160deg, var(--gold-light) 0%, var(--gold) 30%, var(--ink) 55%, var(--gold-deep) 80%, var(--ink) 100%);
  }
  .card--back .card__pattern {
    background: linear-gradient(160deg, var(--pink) 0%, var(--ink) 35%, var(--pink) 65%, var(--ink) 100%);
  }
  .card__content {
    position: relative;
    height: 100%;
    display: flex;
    flex-direction: column;
    align-items: center;
    justify-content: center;
    text-align: center;
  }
  .brand-name {
    margin: 0;
    font-weight: 800;
    line-height: 1;
  }
  .card--front .brand-name {
    font-size: 86px;
    color: var(--pink);
  }
  .card--back .card__content {
    justify-content: flex-start;
    padding-top: 52px;
    box-sizing: border-box;
  }
  .card--back .brand-name {
    font-size: 44px;
    color: var(--gold);
  }
  .byline {
    margin: 6px 0 0;
    font-size: 20px;
    font-weight: 800;
    color: var(--gold);
  }
  .owner-name {
    margin: 0;
    font-size: 30px;
    font-weight: 800;
    color: var(--gold);
  }
  .contact {
    margin: 36px 0 0;
    font-size: 21px;
    font-weight: 800;
    color: var(--white);
    line-height: 1.2;
  }
</style>
</head>
<body>
  <main class="sheet">
    <section class="card card--front">
      <div class="card__pattern" role="img" aria-label="Gold and black zebra stripe pattern"></div>
      <div class="card__content">
        <h1 class="brand-name">Velvette</h1>
      </div>
    </section>

    <section class="card card--back">
      <div class="card__pattern" role="img" aria-label="Hot pink and black zebra stripe pattern"></div>
      <div class="card__content">
        <p class="brand-name">Velvette</p>
        <p class="byline">by</p>
        <p class="owner-name">Marisa Dunn</p>
        <p class="contact">1584 312 760<br>www.velvette.com</p>
      </div>
    </section>
  </main>
</body>
</html>
```